Business cards to launch an education platform

Hi,
I am looking at having new business cards designed.
I am a startup, developing a web platform for schools and university, the education world. It's an online assessment system.
I would like a card that looks classy, and that is using the colors and the font of my logo.

I have attached:
1) my logo
2) A business card that I have designed quickly so you can have all the information required in the card, but I really don't like it.
3) The font that I am using (Lato Regular) to design my web platform
4) Some screenshots of my web platform so you can have a look at the style that I have.

Target Market(s)

Major market: Education system: Schools and university
Minor markets: Business in general

Industry/Entity Type

Business

Contact Information for Business Card

Clara Fenwick
Director

M: 0437 518 902
E: clara.fenwick@amberLoomSystems.com.au

Requirements
Must have
• The colors of my logo

```html
<!DOCTYPE html>
<html lang="en">
<head>
<meta charset="utf-8">
<title>Amber Loom Systems – Business Cards</title>
<link href="https://fonts.googleapis.com/css2?family=Lato:wght@400;700&display=swap" rel="stylesheet">
<style>
  :root {
    --backdrop: #2a2a2c;
    --card: #0e0e10;
    --card-edge: #1a1a1d;
    --brand-blue: #1f8fd6;
    --accent-cyan: #22c2ee;
    --text-white: #f2f4f6;
  }
  * { margin: 0; padding: 0; box-sizing: border-box; }
  html, body {
    width: 1200px;
    height: 900px;
    overflow: hidden;
    background: var(--backdrop);
    font-family: "Lato", sans-serif;
  }
  .card-set {
    position: absolute;
    top: 295px;
    left: 60px;
    display: flex;
    gap: 40px;
  }
  .card {
    position: relative;
    width: 520px;
    height: 310px;
    background: var(--card);
    border: 1px solid var(--card-edge);
    border-radius: 22px;
  }

  /* Front */
  .front .brand-mark {
    position: absolute;
    left: 48px;
    top: 138px;
    display: flex;
    align-items: center;
    gap: 12px;
  }
  .brand-square {
    width: 34px;
    height: 34px;
    background: var(--brand-blue);
  }
  .brand-name {
    font-weight: 700;
    font-size: 18px;
    color: var(--brand-blue);
    letter-spacing: 0.5px;
  }
  .contact-block {
    position: absolute;
    right: 40px;
    top: 70px;
    text-align: right;
  }
  .person-name {
    font-size: 22px;
    font-weight: 400;
    color: var(--accent-cyan);
    line-height: 1.1;
  }
  .person-role {
    font-size: 13px;
    color: var(--text-white);
    margin-top: 2px;
  }
  .contact-list {
    position: absolute;
    right: 40px;
    top: 175px;
    list-style: none;
    text-align: right;
  }
  .contact-item {
    display: flex;
    justify-content: flex-end;
    align-items: center;
    gap: 10px;
    font-size: 14.5px;
    color: var(--text-white);
    margin-bottom: 12px;
  }
  .contact-icon {
    width: 13px;
    height: 13px;
    flex: none;
  }

  /* Back */
  .back .brand-lockup {
    position: absolute;
    inset: 0;
    display: flex;
    align-items: center;
    justify-content: center;
    gap: 16px;
  }
  .back .brand-square {
    width: 52px;
    height: 52px;
  }
  .back .brand-name {
    font-size: 28px;
    letter-spacing: 1.5px;
  }
</style>
</head>
<body>
  <main class="card-set">
    <section class="card front" aria-label="Business card front">
      <div class="brand-mark">
        <span class="brand-square"></span>
        <span class="brand-name">Amber Loom Systems</span>
      </div>
      <div class="contact-block">
        <p class="person-name">Clara Fenwick</p>
        <p class="person-role">Director</p>
      </div>
      <ul class="contact-list">
        <li class="contact-item">
          <span>0437 518 902</span>
          <svg class="contact-icon" viewBox="0 0 24 24" aria-hidden="true">
            <path fill="var(--accent-cyan)" d="M6.6 10.8a15.1 15.1 0 0 0 6.6 6.6l2.2-2.2a1 1 0 0 1 1-.25 11.4 11.4 0 0 0 3.6.57 1 1 0 0 1 1 1V20a1 1 0 0 1-1 1A17 17 0 0 1 3 4a1 1 0 0 1 1-1h3.5a1 1 0 0 1 1 1c0 1.25.2 2.45.57 3.57a1 1 0 0 1-.25 1z"/>
          </svg>
        </li>
        <li class="contact-item">
          <span>clara.fenwick@amberLoomSystems.com.au</span>
          <svg class="contact-icon" viewBox="0 0 24 24" aria-hidden="true">
            <rect x="2" y="5" width="20" height="14" rx="2" fill="var(--accent-cyan)"/>
            <path d="M3 6.5l9 6.5 9-6.5" fill="none" stroke="var(--card)" stroke-width="1.8"/>
          </svg>
        </li>
      </ul>
    </section>

    <section class="card back" aria-label="Business card back">
      <div class="brand-lockup">
        <span class="brand-square"></span>
        <span class="brand-name">Amber Loom Systems</span>
      </div>
    </section>
  </main>
</body>
</html>
```